BOLD & MINIMALIST DESIGN NEEDED

We want a very bold but minimalistic business card design that is impactful and utilizes both sides of the business card. Our current logo is included for your use.

We want bold fonts and good use of negative space. We don't want the logo to overpower the design.

Target Market(s)

Professionals who are building new commercial buildings.

Industry/Entity Type

Construction

Contact Information for Business Card

Name, Title, email, office phone, cell phone, website

Font styles to use
Serif
Sans Serif

Requirements
Must have
• Bold design!

```html
<!DOCTYPE html>
<html lang="en">
<head>
<meta charset="utf-8">
<title>Summitcrest Business Card</title>
<link href="https://fonts.googleapis.com/css2?family=Arimo:wght@400;700&display=swap" rel="stylesheet">
<style>
  :root {
    --backdrop: #dedede;
    --card-white: #ffffff;
    --card-dark: #2f2f2f;
    --ink: #141414;
    --ink-soft: #4a4a4a;
    --rule: #c9c9c9;
    --green: #7cc12a;
    --green-light: #b4e06a;
    --band-black: #111111;
  }
  * { box-sizing: border-box; margin: 0; padding: 0; }
  html, body {
    width: 1200px;
    height: 1200px;
    overflow: hidden;
  }
  body {
    background: var(--backdrop);
    font-family: "Arimo", Arial, sans-serif;
    position: relative;
  }
  .card {
    position: absolute;
    left: 262px;
    width: 688px;
    height: 393px;
    overflow: hidden;
  }
  .card--front {
    top: 159px;
    background: var(--card-white);
  }
  .card--back {
    top: 653px;
    background: var(--card-dark);
  }

  /* Front */
  .brand {
    position: absolute;
    left: 404px;
    top: 134px;
    display: flex;
    align-items: center;
    gap: 10px;
    font-weight: 700;
    font-size: 30px;
    letter-spacing: 0.5px;
    color: var(--ink);
    text-transform: uppercase;
  }
  .brand__square {
    width: 16px;
    height: 16px;
    background: var(--green);
  }
  .person {
    position: absolute;
    left: 48px;
    top: 220px;
  }
  .person__name {
    font-weight: 700;
    font-size: 27px;
    letter-spacing: 0.3px;
    color: var(--ink);
    line-height: 1;
  }
  .person__title {
    margin-top: 6px;
    font-size: 16px;
    color: var(--green);
  }
  .divider {
    position: absolute;
    left: 48px;
    top: 280px;
    width: 596px;
    height: 1px;
    background: var(--rule);
  }
  .contacts {
    position: absolute;
    left: 48px;
    top: 290px;
    list-style: none;
  }
  .contacts__item {
    display: flex;
    align-items: center;
    height: 20px;
    font-size: 16px;
    color: var(--ink-soft);
  }
  .contacts__icon {
    width: 14px;
    height: 14px;
    margin-right: 8px;
    fill: var(--ink);
  }
  .footer-band {
    position: absolute;
    left: 0;
    bottom: 0;
    width: 688px;
    height: 31px;
  }
  .footer-band__url {
    position: absolute;
    right: 42px;
    bottom: 7px;
    font-size: 16px;
    color: var(--card-white);
  }

  /* Back */
  .brand-back {
    position: absolute;
    left: 0;
    right: 0;
    top: 180px;
    display: flex;
    justify-content: center;
    align-items: center;
    gap: 14px;
    font-weight: 700;
    font-size: 44px;
    letter-spacing: 1px;
    color: var(--card-white);
    text-transform: uppercase;
  }
  .brand-back__square {
    width: 22px;
    height: 22px;
    background: var(--green);
  }
  .back-url {
    position: absolute;
    left: 0;
    right: 0;
    top: 333px;
    text-align: center;
    font-size: 16px;
    letter-spacing: 3px;
    color: var(--card-white);
  }
  .back-url__domain {
    color: var(--green);
    font-weight: 700;
  }
</style>
</head>
<body>

<section class="card card--front" aria-label="Business card front">
  <div class="brand">
    <span class="brand__square"></span>
    <span class="brand__name">Summitcrest</span>
  </div>

  <div class="person">
    <p class="person__name">DANIEL REYES</p>
    <p class="person__title">President</p>
  </div>

  <div class="divider"></div>

  <ul class="contacts">
    <li class="contacts__item">
      <svg class="contacts__icon" viewBox="0 0 24 24" aria-hidden="true"><path d="M6.6 10.8a15 15 0 0 0 6.6 6.6l2.2-2.2a1 1 0 0 1 1-.25 11.4 11.4 0 0 0 3.6.57 1 1 0 0 1 1 1V20a1 1 0 0 1-1 1A17 17 0 0 1 3 4a1 1 0 0 1 1-1h3.5a1 1 0 0 1 1 1c0 1.25.2 2.45.57 3.6a1 1 0 0 1-.25 1z"/></svg>
      555-214-7830
    </li>
    <li class="contacts__item">
      <svg class="contacts__icon" viewBox="0 0 24 24" aria-hidden="true"><path d="M7 1h10a2 2 0 0 1 2 2v18a2 2 0 0 1-2 2H7a2 2 0 0 1-2-2V3a2 2 0 0 1 2-2zm0 3v14h10V4zm5 15.2a1.2 1.2 0 1 0 0 2.4 1.2 1.2 0 0 0 0-2.4z"/></svg>
      555-214-7861
    </li>
    <li class="contacts__item">
      <svg class="contacts__icon" viewBox="0 0 24 24" aria-hidden="true"><path d="M2 5h20v14H2zm2 2v.4l8 5.2 8-5.2V7zm0 2.8V17h16V9.8l-8 5.2z"/></svg>
      info@summitcrest.com
    </li>
  </ul>

  <div class="footer-band">
    <svg width="688" height="31" viewBox="0 0 688 31" aria-hidden="true">
      <defs>
        <linearGradient id="greenBand" x1="0" y1="0" x2="1" y2="0">
          <stop offset="0" stop-color="var(--green)"/>
          <stop offset="0.55" stop-color="var(--green-light)"/>
          <stop offset="1" stop-color="var(--green)"/>
        </linearGradient>
      </defs>
      <rect x="0" y="0" width="440" height="15" fill="url(#greenBand)"/>
      <rect x="0" y="15" width="688" height="16" fill="var(--band-black)"/>
      <path d="M446 0 H688 V31 H430 Q440 28 442 12 Q443 2 446 0 Z" fill="var(--band-black)"/>
    </svg>
    <span class="footer-band__url">www.summitcrest.com</span>
  </div>
</section>

<section class="card card--back" aria-label="Business card back">
  <div class="brand-back">
    <span class="brand-back__square"></span>
    <span class="brand-back__name">Summitcrest</span>
  </div>
  <p class="back-url">www.<span class="back-url__domain">summitcrest</span>.com</p>
</section>

</body>
</html>
```